Tuition Center Website

We need a new web site for a tutoring company based in sydney.

We only teach senior highschool students and pride ourselves on building the students abilities to think their way through life.

I would like a bright and vibrant website that looks professional and modern.
It needs to look simple and neat but also have the functionality we need.
Images and flash would be good.

Please keep in mind that the site must be appealing to a younger audience.

We need a multipage website with the following navigation bars:

1.Home (As logo not "home" button)
I would like a news box/ticker somewhere that can stream our chatterbook and pipstream feeds and also any news updates we want to put up.
Subscribe to newsletter button.

2. About us.
This needs to be a pull down into:
-What we do
-Why we do it
-How we do it

3. Courses
Pulldown into:
-Maths
-English
-Science
(we may need to attach extra pages behind these e.g. Courses/Science/Physics or Courses/Science/Chemistry and possibly add a link to a new zandlo form)

4. Inspired
This page is like a blog page where we can upload videos, links to articles that we find to be inspiring and hopefully will inspire others.

5. Inspire
This is a recruitment page. Only content here.

6. Contact us.
Mapquill map widget and a 'contact us' form

* Our branding requires green close to #12FF3D

***Please have a look at the current website.
@ www.velmorlearning.com.au

Thanks everybody hope the revision of my brief is better and more informative than my last one

Target Market(s)

senior highschool students aged 15-19, parents ( to a lesser degree)

Industry/Entity Type

It Company

Requirements
Must have
• Ability to change content on pages.

The green doesn't have to be everywhere, but it must be obvious that it is our colour.

Nice to have
• Sites with a nicer mix of images and flash will be given more consideration. But then again, if you amaze us, you amaze us and we will go with your design.
Should not have
• Should stay away from ocre, brown colours and serif fonts.

```html
<!DOCTYPE html>
<html lang="en">
<head>
<meta charset="utf-8">
<title>Velmor Learning — HSC tutoring &amp; mentoring</title>
<link rel="stylesheet" href="https://fonts.googleapis.com/css2?family=Open+Sans:ital,wght@0,400;0,600;0,700;0,800;1,400;1,700&family=Lobster&display=swap">
<style>
:root{
  --green:#5ad70a;
  --green-dark:#4a9a0c;
  --green-band:#4fb50d;
  --brand:#12ff3d;
  --ink:#1f1f1f;
  --charcoal:#2b2b2b;
  --night:#141414;
  --panel:#ececec;
  --white:#fff;
}
*{margin:0;padding:0;box-sizing:border-box}
html,body{width:913px;height:1200px;overflow:hidden;background:var(--white)}
body{position:relative;font-family:'Open Sans',Arial,sans-serif;color:var(--ink)}
.abs{position:absolute}
a{color:inherit;text-decoration:none}

/* top utility links */
.util-bar{left:228px;top:0;width:614px;height:24px;background:#e6e6e6;border-radius:0 0 14px 14px;display:flex;justify-content:center;align-items:center;font-size:8.3px;color:#444;white-space:nowrap}
.util-bar a{padding:0 5px;border-left:1px solid #c9c9c9}
.util-bar a:first-child{border-left:0}

/* brand */
.brand{left:102px;top:14px;width:120px}
.brand-mark{display:block;width:88px;height:80px;background:var(--green);margin-left:12px}
.brand-name{display:block;margin-top:6px;font-weight:700;font-size:19px;line-height:19px;color:var(--green-dark);text-align:center}

.contact-head{right:93px;top:38px;text-align:right;font-size:13.5px;line-height:17px}
.contact-head a{color:#1a44d8;text-decoration:underline}

/* main navigation */
.main-nav{left:252px;top:84px;width:661px;height:47px;background:linear-gradient(#6fe01a,#3fae0a);clip-path:polygon(22px 0,100% 0,100% 100%,22px 100%,0 50%);display:flex;padding-left:50px;border-bottom:2px solid #2f7d06}
.main-nav a{display:flex;align-items:center;gap:8px;color:var(--white);font-size:17.5px;padding:0 18px;border-right:1px solid #3a8f08}
.main-nav a:last-child{border-right:0}
.main-nav svg{width:20px;height:20px}

.rule-dark{left:0;top:142px;width:913px;height:4px;background:var(--night)}

/* hero */
.hero-art{left:0;top:146px;width:913px;height:362px;background:linear-gradient(90deg,#8a6a55 0%,#6b5a50 22%,#3d4448 42%,#2e3438 70%,#23282b 100%)}
.hero-copy{left:440px;top:190px;width:400px;color:var(--white)}
.hero-title{font-weight:800;font-size:56px;line-height:56px;color:var(--green);letter-spacing:-0.5px}
.hero-sub{font-weight:700;font-size:19.5px;color:#7ccf1e;margin-top:2px}
.hero-text{font-size:16px;line-height:19.3px;margin-top:12px}
.hero-text b{font-style:italic;font-weight:700}
.btn-enquire{left:436px;top:421px;width:183px;height:38px;background:linear-gradient(#5fcf12,#3a9a08);border-bottom:3px solid #2a6e05;color:var(--white);font-weight:700;font-size:20px;display:flex;align-items:center;justify-content:center}
.band-green{left:0;top:508px;width:913px;height:8px;background:var(--green-band)}

/* intro */
.intro{left:110px;top:536px;width:470px;font-size:16.5px;line-height:20.5px}
.intro .hsc{color:var(--green-dark);font-weight:700}
.intro b{font-style:italic}
.beliefs{top:604px;width:240px}
.beliefs h3{font-family:'Lobster',cursive;font-weight:400;font-size:24px;color:var(--green-dark);margin-bottom:10px}
.beliefs ul{list-style:none;font-size:12.3px;line-height:20.6px}
.beliefs li{display:flex;gap:8px;align-items:flex-start}
.beliefs svg{flex:none;width:16px;height:14px;margin-top:3px}
.beliefs .wrap{padding-left:13px;display:block}

/* trial box */
.trial{left:599px;top:532px;width:223px;height:178px;background:linear-gradient(#141414 70%,#4a4a4a);border-radius:3px;padding:10px 13px;color:var(--white)}
.trial h4{font-family:'Lobster',cursive;font-weight:400;font-size:20px;line-height:21px}
.trial h5{font-weight:700;font-size:23px;line-height:24px;color:var(--brand)}
.trial p{font-size:12px;line-height:16px;margin-top:6px}
.trial a{display:inline-block;margin-top:8px;background:var(--green-dark);font-weight:700;font-size:12.5px;padding:5px 9px}

/* feature panel */
.feature{left:91px;top:739px;width:737px;height:244px;background:var(--panel)}
.news{left:104px;top:754px;width:235px;height:214px;background:var(--green-dark);padding:22px 10px 0 22px;color:var(--white)}
.news h3{font-weight:600;font-size:20px;margin-bottom:12px}
.news ul{list-style:none;font-size:11.5px;line-height:20.6px;white-space:nowrap}
.news li{display:flex;align-items:center;gap:8px}
.news li::before{content:"";width:7px;height:7px;border-radius:50%;background:var(--brand);flex:none}
.quotes{left:361px;top:764px;width:214px}
.quotes h3{font-weight:700;font-size:21px;line-height:20px}
.quotes p{font-size:10.3px;line-height:15px;margin-top:14px}
.quotes cite{display:block;margin-top:14px;font-size:10.3px;color:var(--green-dark)}
.slider{left:360px;top:939px;width:214px;height:23px;background:#cfcfcf}
.slider svg{position:absolute;right:4px;top:3px}
.feed{left:588px;top:754px;width:228px;height:211px;background:var(--white);border:1px solid #bbb;border-top:2px solid #3b5b9a;font-size:9.6px}
.feed-head{display:flex;gap:8px;padding:8px 8px 6px;border-bottom:1px solid #ddd}
.feed-mark{width:26px;height:26px;background:var(--green);flex:none}
.feed-title{color:#3b5b9a;font-weight:600;font-size:10.5px}
.feed-like{margin-top:4px;font-size:8.5px;color:#333}
.feed-like span{border:1px solid #aab;padding:1px 4px;margin-right:4px;color:#3b5b9a}
.feed-post{display:flex;gap:8px;padding:8px 16px 0 8px;line-height:13.6px;color:#333}
.feed-post .feed-mark{margin-top:2px}
.feed-foot{position:absolute;left:8px;bottom:3px;font-size:7.5px;color:#3b5b9a}
.feed-scroll{position:absolute;right:2px;top:56px;width:8px;height:136px;background:#eee;border-left:1px solid #ddd}

/* footer */
.footer{left:0;top:995px;width:913px;height:163px;background:var(--charcoal)}
.foot-col{color:var(--white)}
.foot-col h4{font-weight:600;font-size:15px;color:var(--white);padding-bottom:4px;border-bottom:1px solid #bbb;width:268px}
.sitemap{left:141px;top:1019px}
.sitemap ul{list-style:none;font-size:11.3px;line-height:19.8px;margin-top:8px}
.reach{left:495px;top:1019px}
.map-area{left:496px;top:1053px;width:114px;height:76px;background:linear-gradient(135deg,#dfe4dc,#c9cfc4)}
.reach-list{left:622px;top:1051px;font-size:10.1px;line-height:15.9px;color:#eee}
.reach-list div{display:flex;gap:6px}
.reach-list svg{width:9px;height:9px;margin-top:3px;flex:none}
.reach-list a{text-decoration:underline}
.rule-green{left:0;top:1157px;width:913px;height:3px;background:var(--green-band)}
.base{left:0;top:1160px;width:913px;height:40px;background:var(--night);color:var(--white);font-size:12px}
.base .copy{position:absolute;left:112px;top:12px}
.base .follow{position:absolute;right:104px;top:13px;display:flex;gap:8px;align-items:center;font-size:10.5px}
.base .follow strong{font-weight:400;font-size:12px;margin-right:4px}
.base .follow a{color:#ddd}
</style>
</head>
<body>

<nav class="abs util-bar">
  <a href="#">Board Past HSC Papers</a><a href="#">State Students Online</a><a href="#">UniPath</a><a href="#">HSC Hub Online [Study Resources]</a><a href="#">Help for Study Stress</a><a href="#">Velmor on chatterbook</a>
</nav>

<a class="abs brand" href="#"><span class="brand-mark"></span><span class="brand-name">velmor learning</span></a>

<div class="abs contact-head">Phone: (02) 8000 4812<br>Email: <a href="#">learn@velmorlearning.com.au</a></div>

<nav class="abs main-nav">
  <a href="#"><svg viewBox="0 0 20 20"><rect x="4" y="2" width="12" height="16" rx="1" fill="#fff"/><path d="M7 7h6M7 10h6M7 13h4" stroke="#4fb50d" stroke-width="1.4"/></svg>About us</a>
  <a href="#"><svg viewBox="0 0 20 20"><rect x="1" y="4" width="18" height="12" rx="1" fill="#fff"/><path d="M4 8h7M4 11h5" stroke="#4fb50d" stroke-width="1.4"/></svg>Courses</a>
  <a href="#"><svg viewBox="0 0 20 20"><circle cx="10" cy="8" r="6" fill="#fff"/><rect x="7.5" y="14" width="5" height="4" fill="#fff"/></svg>Inspired</a>
  <a href="#"><svg viewBox="0 0 20 20"><circle cx="10" cy="10" r="9" fill="#fff"/><path d="M7 5l2 3-1.2 1.2a6 6 0 003 3L12 11l3 2-1.5 2C10 15 5 10 5 6.5z" fill="#3fae0a"/></svg>Contact Us</a>
</nav>

<div class="abs rule-dark"></div>

<div class="abs hero-art" role="img" aria-label="Photo of a smiling student writing maths on a chalkboard"></div>
<div class="abs hero-copy">
  <h1 class="hero-title">i am velmor.</h1>
  <p class="hero-sub">real HSC coaching &amp; mentoring.</p>
  <p class="hero-text">The HSC help you need, in the years you need it. We offer <b>small classes, individualised attention and genuine care</b> for each student. It's different - in a good way. Feel free to find out more about us, and let us know if there's any way we can help you on your journey.</p>
</div>
<a class="abs btn-enquire" href="#">Enquire Now</a>
<div class="abs band-green"></div>

<p class="abs intro">Velmor Learning are <span class="hsc">HSC</span> mentors and tutors who aim to <b>build real relationships</b> and offer you the help you need. <span class="hsc">HSC</span> tutoring is different at Velmor – in a good way.</p>

<section class="abs beliefs" style="left:108px">
  <h3>We Don't Believe In:</h3>
  <ul>
    <li><svg viewBox="0 0 16 14"><path d="M1 5v8h12V9" fill="none" stroke="#4fb50d" stroke-width="2"/><path d="M5 9l7-6M8 2h5v5" fill="none" stroke="#4fb50d" stroke-width="2"/></svg>Massive classes;</li>
    <li><svg viewBox="0 0 16 14"><path d="M1 5v8h12V9" fill="none" stroke="#4fb50d" stroke-width="2"/><path d="M5 9l7-6M8 2h5v5" fill="none" stroke="#4fb50d" stroke-width="2"/></svg>Spoon-feeding answers;</li>
    <li><svg viewBox="0 0 16 14"><path d="M1 5v8h12V9" fill="none" stroke="#4fb50d" stroke-width="2"/><path d="M5 9l7-6M8 2h5v5" fill="none" stroke="#4fb50d" stroke-width="2"/></svg>One-size-fits-all teaching.</li>
  </ul>
</section>
<section class="abs beliefs" style="left:343px;width:240px">
  <h3>We Do Believe In:</h3>
  <ul>
    <li><svg viewBox="0 0 16 14"><path d="M1 5v8h12V9" fill="none" stroke="#4fb50d" stroke-width="2"/><path d="M5 9l7-6M8 2h5v5" fill="none" stroke="#4fb50d" stroke-width="2"/></svg>Small classes tailored to you;</li>
    <li><svg viewBox="0 0 16 14"><path d="M1 5v8h12V9" fill="none" stroke="#4fb50d" stroke-width="2"/><path d="M5 9l7-6M8 2h5v5" fill="none" stroke="#4fb50d" stroke-width="2"/></svg>Helping you think for yourself;</li>
    <li><svg viewBox="0 0 16 14"><path d="M1 5v8h12V9" fill="none" stroke="#4fb50d" stroke-width="2"/><path d="M5 9l7-6M8 2h5v5" fill="none" stroke="#4fb50d" stroke-width="2"/></svg>Genuinely caring about who you are</li>
    <li><span class="wrap">as an individual.</span></li>
  </ul>
</section>

<aside class="abs trial">
  <h4>Ask For Your</h4>
  <h5>Free Trial Lesson</h5>
  <p>Because we believe you shouldn't have to sign up until you see what it's actually like. Call or email us now!</p>
  <a href="#">Send an Enquiry</a>
</aside>

<div class="abs feature"></div>
<section class="abs news">
  <h3>Recent News</h3>
  <ul>
    <li>Year 11 FREE HSC Workshops!</li>
    <li>Uni Open Days 2012</li>
    <li>Considering Studying Interstate?</li>
    <li>Year 11 FREE HSC Workshops!</li>
    <li>Considering Studying Interstate?</li>
    <li>Uni Open Days 2012</li>
  </ul>
</section>
<section class="abs quotes">
  <h3>What Our Students Say</h3>
  <p>I like the support the most, how the people and teachers here pick you off your feet, make you do better and tell you that it's not the end of the world!!</p>
  <cite>~Maren, Ashcombe Girls HS</cite>
</section>
<div class="abs slider"><svg width="42" height="17" viewBox="0 0 42 17"><circle cx="8.5" cy="8.5" r="8" fill="#555"/><circle cx="29.5" cy="8.5" r="8" fill="#555"/><path d="M10 4.5l-4 4 4 4M28 4.5l4 4-4 4" fill="none" stroke="#fff" stroke-width="1.8"/></svg></div>

<section class="abs feed">
  <div class="feed-head"><span class="feed-mark"></span><div><div class="feed-title">chatterbook in HSC</div><div class="feed-like"><span>Like</span>581,163</div></div></div>
  <div class="feed-post"><span class="feed-mark"></span><div><div class="feed-title">chatterbook in HSC</div>chatterbook and the Harlow Family Trust are thrilled to open registration for CodeJam 2.0 on April 9, 2013. Please share this with anyone who may be interested in fielding a team. Jam on!</div></div>
  <div class="feed-scroll"></div>
  <div class="feed-foot">chatterbook social plugin</div>
</section>

<footer class="abs footer"></footer>
<section class="abs sitemap foot-col">
  <h4>Site Map</h4>
  <ul><li>Home</li><li>About us</li><li>Courses</li><li>Inspired</li><li>Contact Us</li></ul>
</section>
<section class="abs reach foot-col"><h4>Contact Us</h4></section>
<div class="abs map-area" role="img" aria-label="Mapquill street map marking the centre's location"></div>
<div class="abs reach-list">
  <div><svg viewBox="0 0 9 9"><path d="M4.5 0a3 3 0 013 3c0 2-3 6-3 6s-3-4-3-6a3 3 0 013-3z" fill="#fff"/></svg><span>Street: 42 Larkfield Rd<br>Ashcombe NSW 2199</span></div>
  <div><svg viewBox="0 0 9 9"><circle cx="4.5" cy="4.5" r="4.5" fill="#fff"/></svg><span>Phone: (02) 8000 4812</span></div>
  <div><svg viewBox="0 0 9 9"><rect y="1.5" width="9" height="6" fill="#fff"/></svg><span>Email: <a href="#">learn@velmorlearning.com.au</a></span></div>
</div>
<div class="abs rule-green"></div>
<div class="abs base">
  <span class="copy">© 2013 velmor learning | HSC tutoring &amp; mentoring</span>
  <span class="follow"><strong>Follow us</strong><a href="#">chatterbook</a><a href="#">pipstream</a><a href="#">vidloop</a><a href="#">linkpro</a></span>
</div>

</body>
</html>
```